Updated website design needed for Radiology Group, Pine Hollow Imaging Partners

Clean, uncluttered, updated design needed for top regional Radiology Center. Focus on personal, patient oriented design, (not clinical). Should be simple and easy to navigate, with clear CTAs. Use blues, greens and photos of people in the Central Oregon outdoors.
Uncoded, PSD design only. 2 pages: Home page and one example interior page.
reference current site: http://www.phipclinic-example.com/
Sites they like:
http://www.valescanlabs-example.com/
http://www.tbmx-example.net/handler.cfm?event=practice,main
http://www.kestrelbonecare-example.com/

Medical Imaging

2 page

Sans Serif

• Personal and patient friendly.
• Lots of white space, clean and uncluttered. Clear CTAs, such as: Patient Bill Pay, Make an Appointment, Meet Our Doctors
• Use copy and contact information from the current site.
• Use outdoor images from Central Oregon, late Winter/ Spring (snow, light colors, spring green, for example)
• Include one example interior page, either Your Exam or Meet Our Doctors
• The client likes:
• Meet Our Doctors slider section, and big, easy to navigate Information Center on www.kestrelbonecare-example.com
• The personal feel of the Your Exam section on www.valescanlabs-example.com
• Blues and Greens, outdoorsy imagery
• The client does not like:
• complex drop down menus
• clinical feel
• Do not use lorum ipsum or dummy text.
• Do not use outdoor images from other regions. Do not use Summer (hot, poolside) or Fall (red/orange leaves) images.

```html
<!DOCTYPE html>
<html lang="en">
<head>
<meta charset="utf-8">
<title>Pine Hollow Imaging Partners</title>
<link href="https://fonts.googleapis.com/css2?family=Titillium+Web:wght@400;600;700;900&family=Lato:wght@400;700&display=swap" rel="stylesheet">
<style>
:root{
  --blue:#13b9f2;
  --blue-dark:#0a9fd4;
  --green:#8cbd00;
  --ink:#333;
  --services-bg:#e9ecf3;
  --reviews-bg:#efefef;
  --footer:#2e2e2e;
  --footer-bottom:#1f1f1f;
  --white:#fff;
}
*{margin:0;padding:0;box-sizing:border-box}
html,body{width:1200px;height:2616px;overflow:hidden}
body{position:relative;background:var(--white);font-family:'Lato',sans-serif;color:var(--ink)}
.abs{position:absolute}
h2.section-title{font-family:'Titillium Web',sans-serif;font-weight:400;font-size:29px;color:#222;text-align:center}
.divider{position:absolute;left:50%;transform:translateX(-50%);width:420px;height:20px}
.divider::before{content:"";position:absolute;left:0;right:0;top:9px;height:1px;background:#c9ccd3}
.divider::after{content:"";position:absolute;left:50%;top:2px;width:16px;height:16px;margin-left:-8px;border-radius:50%;background:#5d6f95;box-shadow:0 0 0 5px #fff}
.services .divider::after{box-shadow:0 0 0 5px var(--services-bg)}
.reviews .divider::after{box-shadow:0 0 0 5px var(--reviews-bg)}
.btn{display:inline-block;font-family:'Lato',sans-serif;font-weight:700;font-size:12px;text-decoration:none}

/* header */
.topline{left:0;top:0;width:1200px;height:3px;background:#444}
.logo{left:160px;top:17px;display:flex;align-items:center;gap:12px}
.logo-mark{width:58px;height:62px;background:#6c7aa6}
.logo-name{font-family:'Titillium Web',sans-serif;font-weight:600;font-size:19px;line-height:21px;color:#3b4a78;width:150px}
.top-cta{left:703px;top:0;height:31px;display:flex}
.top-phone{background:var(--blue);color:#fff;font-weight:700;font-size:16px;display:flex;align-items:center;gap:10px;padding:0 20px 0 14px;border-radius:16px 0 0 16px}
.top-book{background:var(--green);color:#fff;font-weight:700;font-size:13px;display:flex;align-items:center;padding:0 26px 0 20px;clip-path:polygon(0 0,100% 0,92% 100%,0 100%)}

/* nav */
.nav{left:0;top:98px;width:1200px;height:38px;background:var(--blue);display:flex;padding-left:143px}
.nav a{color:#fff;text-decoration:none;font-size:11.5px;padding:0 13px;display:flex;align-items:center}
.nav a.active{background:var(--green);font-weight:700;padding:0 17px}

/* hero */
.hero{left:0;top:136px;width:1200px;height:410px;
  background:
    radial-gradient(ellipse 45% 25% at 45% 62%,rgba(240,170,40,.55),transparent 70%),
    radial-gradient(ellipse 40% 20% at 55% 78%,rgba(60,170,220,.7),transparent 70%),
    linear-gradient(180deg,#a9cfe6 0%,#5e8a45 14%,#35612a 32%,#6f9a3c 44%,#2d6f94 58%,#1d5f88 74%,#3aa6d0 100%)}
.hero-caption{left:0;top:326px;width:1200px;height:84px;background:rgba(20,30,40,.55);color:#fff;font-family:'Titillium Web',sans-serif;font-size:27px;line-height:36px;text-align:center;padding-top:6px}
.hero-arrow{top:164px;width:24px;height:48px}

/* welcome */
.welcome-title{left:0;top:590px;width:1200px}
.welcome-text{left:169px;top:683px;width:863px;font-size:13.2px;line-height:22.5px;color:#444;text-align:center}
.welcome-btn{left:549px;top:790px;width:100px;height:33px;background:var(--blue);color:#fff;line-height:33px;text-align:center}

/* services */
.services{left:0;top:877px;width:1200px;height:550px;background:var(--services-bg)}
.service-card{width:285px;height:183px;background:#fff;padding:6px 6px 0}
.service-photo{height:119px}
.service-label{position:absolute;left:0;bottom:0;width:285px;height:52px;background:var(--blue);color:#fff;font-size:19px;text-align:center;line-height:52px}
.service-card.featured .service-label{background:var(--green)}

/* audience */
.audience{top:1427px;width:600px;height:338px;color:#fff;text-align:center}
.audience.patients{left:0;background:radial-gradient(ellipse 40% 60% at 25% 45%,rgba(150,140,125,.55),transparent 70%),linear-gradient(135deg,#6e6b66,#55524e 55%,#3d3d3c)}
.audience.physicians{left:600px;background:radial-gradient(ellipse 35% 55% at 80% 40%,rgba(255,255,255,.25),transparent 70%),radial-gradient(ellipse 30% 50% at 15% 55%,rgba(255,255,255,.18),transparent 70%),linear-gradient(135deg,#5cc9f2,#1fb5ee 60%,#12a9e6)}
.audience svg{display:block;margin:34px auto 0}
.audience h3{font-family:'Titillium Web',sans-serif;font-weight:900;font-size:29px;margin-top:14px;letter-spacing:.5px}
.audience p{font-size:14px;line-height:25px;width:420px;margin:4px auto 0}
.audience .btn{margin-top:19px;width:100px;height:33px;line-height:33px;background:#fff;color:#333}

/* bill pay + physicians */
.col-title{font-family:'Titillium Web',sans-serif;font-weight:400;font-size:27px;color:#222;padding-bottom:6px;border-bottom:1px solid #d6d6d6}
.billpay{left:160px;top:1806px;width:405px}
.billpay-photo{left:160px;top:1859px;width:198px;height:133px;background:radial-gradient(ellipse 35% 30% at 45% 30%,rgba(40,110,200,.55),transparent 70%),radial-gradient(ellipse 30% 35% at 75% 45%,rgba(235,190,160,.7),transparent 70%),linear-gradient(160deg,#f2f6fa,#cfdbe6 55%,#8ea6ba)}
.billpay-links{left:372px;top:1865px;list-style:none}
.billpay-links li{font-size:11px;line-height:18px;font-weight:700;margin-bottom:16px;display:flex;gap:8px;width:170px}
.billpay-links li::before{content:"➝";color:var(--blue);font-size:10px}
.billpay-links a{color:#333;text-decoration:underline}
.team{left:628px;top:1806px;width:410px}
.doctor{top:1866px;width:96px;height:119px;background:radial-gradient(ellipse 30% 22% at 50% 30%,rgba(225,185,160,.8),transparent 75%),linear-gradient(180deg,#eef2f5 0%,#e4eaef 45%,#ffffff 60%,#c8d8e6 100%)}
.doctor span{position:absolute;left:0;bottom:0;width:96px;height:19px;background:var(--blue);color:#fff;font-size:10px;line-height:19px;text-align:center}

/* reviews */
.reviews{left:0;top:2044px;width:1200px;height:290px;background:var(--reviews-bg)}
.avatar{left:169px;top:2135px;width:110px;height:110px;border-radius:50%;background:radial-gradient(circle at 50% 40%,#e3c4ad 0,#d2ae96 22%,transparent 34%),linear-gradient(180deg,#f3f4f5,#cdd5dc);border:4px solid #2e2e2e}
.review-text{left:319px;top:2148px;width:712px;font-size:11.8px;line-height:21px;color:#333}
.review-text .quote{font-family:'Titillium Web',sans-serif;font-size:44px;color:#c9ccd3;line-height:10px;vertical-align:-16px;margin-right:6px}
.review-rule{left:319px;top:2240px;width:712px;height:1px;background:#d3d3d3}
.review-name{left:319px;top:2248px;font-size:15px;font-weight:700;color:var(--blue);font-style:italic}
.dots{left:998px;top:2276px;display:flex;gap:5px}
.dots i{width:8px;height:8px;border-radius:50%;background:#bbb}
.dots i.on{background:#fff;border:2px solid #4bb89a}

/* footer */
.footer-shape{left:0;top:2300px;width:1200px;height:280px}
.foot-col h4{font-family:'Lato',sans-serif;font-weight:700;font-size:14px;color:#fff;padding-bottom:8px;border-bottom:1px solid #555;width:220px}
.foot-links{display:flex;gap:30px;margin-top:12px}
.foot-links ul{list-style:none}
.foot-links li{font-size:11px;color:#ddd;line-height:22.5px}
.foot-links li::before{content:"›";margin-right:8px;color:#aaa}
.foot-sep{width:1px;height:150px;background:#555;top:2402px}
.field{width:190px;height:20px;background:#fff;border-radius:2px;font-size:9px;color:#999;padding:4px 7px;font-style:italic}
.submit{background:var(--green);color:#fff;font-size:10px;padding:3px 9px;border-radius:2px;display:inline-block}
.contact-row{display:flex;gap:12px;font-size:11px;color:#ddd;line-height:17px;margin-top:14px}
.contact-row svg{flex:none;margin-top:2px}
.bottom-bar{left:0;top:2578px;width:1200px;height:38px;background:var(--footer-bottom)}
.copyright{left:163px;top:12px;font-size:11px;color:#ccc}
.social{top:7px;width:26px;height:26px;border-radius:50%}
</style>
</head>
<body>

<header>
  <div class="abs topline"></div>
  <div class="abs logo">
    <span class="logo-mark"></span>
    <span class="logo-name">Pine Hollow Imaging Partners</span>
  </div>
  <div class="abs top-cta">
    <div class="top-phone">
      <svg width="16" height="16" viewBox="0 0 24 24"><circle cx="12" cy="12" r="12" fill="#fff"/><path d="M8 6l2 0 1 3-1.5 1a8 8 0 004 4L15 12.5l3 1v2a1.5 1.5 0 01-1.5 1.5A10 10 0 016.5 7.5 1.5 1.5 0 018 6z" fill="#13b9f2"/></svg>
      555 010 4420
    </div>
    <div class="top-book">Book An Appointment</div>
  </div>
  <nav class="abs nav">
    <a class="active" href="#">Home</a>
    <a href="#">About Us</a>
    <a href="#">Our Services</a>
    <a href="#">For Patients</a>
    <a href="#">Our Physicians</a>
    <a href="#">For Physicians</a>
    <a href="#">PACS &amp; Documents</a>
    <a href="#">Appointments</a>
    <a href="#">Our Locations</a>
  </nav>
</header>

<section class="abs hero" role="img" aria-label="Photo of friends kayaking on a pine-lined lake in Central Oregon in spring">
  <svg class="abs hero-arrow" style="left:118px" viewBox="0 0 24 48"><path d="M20 4L4 24l16 20" fill="none" stroke="#fff" stroke-width="2"/></svg>
  <svg class="abs hero-arrow" style="left:1056px" viewBox="0 0 24 48"><path d="M4 4l16 20L4 44" fill="none" stroke="#fff" stroke-width="2"/></svg>
  <div class="abs hero-caption">Provide Quality Diagnostic Imaging Services To The<br>Central And Eastern Oregon Communities</div>
</section>

<section class="welcome">
  <h2 class="abs section-title welcome-title">Welcome to Pine Hollow Imaging Partners</h2>
  <div class="divider" style="top:643px"></div>
  <p class="abs welcome-text">For more than forty years our radiologists have cared for neighbors across Central and Eastern Oregon. We pair the latest imaging technology with a calm, welcoming setting, so every exam feels personal rather than clinical. Our board-certified physicians read each study close to home, share results quickly with your doctor and take time to answer your questions. From a routine x-ray to an advanced MRI, we are here to help you get back outside.</p>
  <a class="abs btn welcome-btn" href="#">Read More</a>
</section>

<section class="abs services">
  <h2 class="abs section-title" style="left:0;top:30px;width:1200px">Our Services</h2>
  <div class="divider" style="top:78px"></div>
  <div class="abs service-card featured" style="left:160px;top:119px"><div class="service-photo" role="img" aria-label="MRI scanner in a bright room" style="background:radial-gradient(ellipse 30% 45% at 38% 50%,#9aa3ab,transparent 70%),linear-gradient(90deg,#f7f8f9,#dfe3e6 60%,#f2f3f4)"></div><div class="service-label">MRI</div></div>
  <div class="abs service-card" style="left:459px;top:119px"><div class="service-photo" role="img" aria-label="CT scanner" style="background:radial-gradient(ellipse 22% 40% at 70% 42%,#8e969c,transparent 70%),radial-gradient(ellipse 45% 12% at 40% 78%,#c5cacf,transparent 75%),linear-gradient(180deg,#fbfbfb,#e7e9eb)"></div><div class="service-label">CT-64</div></div>
  <div class="abs service-card" style="left:755px;top:119px"><div class="service-photo" role="img" aria-label="X-ray of two hands" style="background:radial-gradient(ellipse 20% 45% at 32% 55%,#8a8a8a,transparent 70%),radial-gradient(ellipse 20% 45% at 68% 55%,#8a8a8a,transparent 70%),linear-gradient(135deg,#1e1e1e,#0b0b0b)"></div><div class="service-label">X-Ray</div></div>
  <div class="abs service-card" style="left:160px;top:328px"><div class="service-photo" role="img" aria-label="Nuclear medicine camera" style="background:radial-gradient(ellipse 28% 40% at 45% 45%,#8fa0a6,transparent 70%),linear-gradient(90deg,#eef1f3,#d1d9dc 70%,#b8c3c8)"></div><div class="service-label">Nuclear Medicine</div></div>
  <div class="abs service-card" style="left:459px;top:328px"><div class="service-photo" role="img" aria-label="PET scanner room" style="background:radial-gradient(ellipse 30% 45% at 62% 55%,#c9ced2,transparent 70%),linear-gradient(90deg,#f3eee8,#e6e9ea 55%,#a9c99a)"></div><div class="service-label">PET</div></div>
  <div class="abs service-card" style="left:755px;top:328px"><div class="service-photo" role="img" aria-label="Ultrasound scan image" style="background:radial-gradient(ellipse 40% 40% at 45% 55%,#777,#2a2a2a 65%,#111)"></div><div class="service-label">Ultrasound</div></div>
</section>

<section class="abs audience patients" role="img" aria-label="Background photo of a patient talking with a clinician">
  <svg width="76" height="74" viewBox="0 0 76 74"><circle cx="12" cy="9" r="7" fill="#fff"/><path d="M4 20h16l10 10-4 4-6-6v42h-6V50h-2v20H6V36l-2-2z" fill="#fff"/><rect x="28" y="6" width="44" height="40" rx="2" fill="none" stroke="#fff" stroke-width="4"/><path d="M50 46l-10 24M50 46l10 24" stroke="#fff" stroke-width="4"/></svg>
  <h3>For Patients</h3>
  <p>Find out how to prepare for your exam, what to expect on the day, and how to reach our friendly staff with any question about results or billing</p>
  <a class="btn" href="#">Read More</a>
</section>
<section class="abs audience physicians" role="img" aria-label="Background photo of a team of physicians">
  <svg width="76" height="74" viewBox="0 0 76 74"><circle cx="12" cy="9" r="7" fill="#fff"/><path d="M4 20h16l10 10-4 4-6-6v42h-6V50h-2v20H6V36l-2-2z" fill="#fff"/><rect x="28" y="6" width="44" height="40" rx="2" fill="none" stroke="#fff" stroke-width="4"/><path d="M50 46l-10 24M50 46l10 24" stroke="#fff" stroke-width="4"/></svg>
  <h3>For Physicians</h3>
  <p>Refer patients online, view studies through our secure image portal and talk directly with the radiologist who read the exam for your patient</p>
  <a class="btn" href="#">Read More</a>
</section>

<section class="bill-team">
  <h3 class="abs col-title billpay">Online Bill Pay</h3>
  <div class="abs billpay-photo" role="img" aria-label="Hand holding a payment card over a laptop"></div>
  <ul class="abs billpay-links">
    <li><a href="#">BILLPAY Pine Hollow Imaging</a></li>
    <li><a href="#">BILLPAY Pine Hollow MRI</a></li>
    <li><a href="#">BILLPAY Juniper Valley Imaging</a></li>
  </ul>
  <h3 class="abs col-title team">Our Physicians</h3>
  <div class="abs doctor" style="left:628px" role="img" aria-label="Portrait of Dr. Nora Whitfield"><span>Nora Whitfield</span></div>
  <div class="abs doctor" style="left:733px" role="img" aria-label="Portrait of Dr. Clara Benning"><span>Clara Benning</span></div>
  <div class="abs doctor" style="left:839px" role="img" aria-label="Portrait of Dr. Owen Marsh"><span>Owen Marsh</span></div>
  <div class="abs doctor" style="left:944px" role="img" aria-label="Portrait of Dr. Elliot Crane"><span>Elliot Crane</span></div>
</section>

<section class="abs reviews">
  <h2 class="abs section-title" style="left:0;top:26px;width:1200px">Patient Reviews</h2>
  <div class="divider" style="top:70px"></div>
</section>
<div class="abs avatar" role="img" aria-label="Portrait of the reviewing patient"></div>
<p class="abs review-text"><span class="quote">“</span>I was nervous about my first MRI, but the whole team made me feel at ease from the moment I walked in. The technologist explained every step, checked on me during the scan and even found me a warm blanket. My results reached my doctor the very next morning, and the radiologist called to walk me through them. It felt like being cared for by neighbors, not a big hospital, and I was back on the trail that week.</p>
<div class="abs review-rule"></div>
<div class="abs review-name">- Mr. Tobias Renwick</div>
<div class="abs dots"><i class="on"></i><i></i><i></i></div>

<footer>
  <svg class="abs footer-shape" viewBox="0 2300 1200 280" preserveAspectRatio="none">
    <path d="M0 2423 Q600 2175 1200 2423" fill="none" stroke="#13b9f2" stroke-width="7"/>
    <path d="M0 2436 Q600 2190 1200 2436 V2580 H0Z" fill="#2e2e2e"/>
  </svg>
  <div class="abs foot-col" style="left:207px;top:2392px">
    <h4>Quick Links</h4>
    <div class="foot-links">
      <ul><li>Home</li><li>About Us</li><li>Our Services</li><li>For Patients</li><li>Our Physicians</li></ul>
      <ul><li>For Physicians</li><li>PACS &amp; Documents</li><li>Appointments</li><li>Our Locations</li></ul>
    </div>
  </div>
  <div class="abs foot-sep" style="left:476px"></div>
  <div class="abs foot-col" style="left:523px;top:2392px">
    <h4>Quick Inquiry</h4>
    <div class="field" style="margin-top:14px">Name</div>
    <div class="field" style="margin-top:6px">Email</div>
    <div class="field" style="margin-top:6px;height:34px">Message</div>
    <div class="submit" style="margin-top:8px">Submit</div>
  </div>
  <div class="abs foot-sep" style="left:764px"></div>
  <div class="abs foot-col" style="left:809px;top:2392px">
    <h4>Contact Details</h4>
    <div class="contact-row"><svg width="10" height="13" viewBox="0 0 10 13"><path d="M5 0a5 5 0 00-5 5c0 4 5 8 5 8s5-4 5-8a5 5 0 00-5-5z" fill="#ddd"/><circle cx="5" cy="5" r="2" fill="#2e2e2e"/></svg><span>2280 NW Juniper Ridge Way<br>Bend, Oregon 97702</span></div>
    <div class="contact-row"><svg width="11" height="11" viewBox="0 0 24 24"><path d="M5 2h4l2 5-3 2a12 12 0 007 7l2-3 5 2v4a2 2 0 01-2 2A19 19 0 013 4a2 2 0 012-2z" fill="#ddd"/></svg><span>(541) 555-0148</span></div>
    <div class="contact-row"><svg width="12" height="9" viewBox="0 0 12 9"><rect width="12" height="9" fill="#ddd"/><path d="M0 0l6 5 6-5" fill="none" stroke="#2e2e2e"/></svg><span>hello@phipclinic-example.com</span></div>
  </div>
  <div class="abs bottom-bar">
    <div class="abs copyright">Copyright © 2016 - Pine Hollow Imaging Partners &nbsp;|&nbsp; All Right Reserved.</div>
    <span class="abs social" style="left:943px;background:var(--green)"></span>
    <span class="abs social" style="left:978px;background:var(--blue)"></span>
    <span class="abs social" style="left:1013px;background:var(--blue-dark)"></span>
  </div>
</footer>

</body>
</html>
```